Fitness Equipment Repair Business Needs a Catchy New Business Card

We have an existing business card, however, it is quite plain and boring. We are expanding primarily in the commercial area (gyms, studios, apartment complexes etc). The business card will serve as eye candy to those managers/owners that can't be met for a face to face.
Originally I was planning for a brochure as well, but all of our information is better summarized on our website. (brightloopservice.ca).
I would like the card to match the colour scheme of the website and utilize the logo. It should have a professional clean feel to it, however, a little colouring outside the lines wouldn't hurt.
The example card is for my service technician (Colin Marsh). If possible I would like to be able to edit the text to use for more than one person.

Industry/Entity Type

Appliance Repair

Contact Information for Business Card

Clean, crisp and professional but needs to be eye catching. Preferably using the black, white and red colour scheme matching the website. Double sided would be nice, but is not necessary.

Colors
ec1f27
ffffff
000000

Requirements
Must have
• Must be able to edit name, phone number and title to use for multiple people. Must show the company website (brightloopservice.ca).

```html
<!DOCTYPE html>
<html lang="en">
<head>
<meta charset="utf-8">
<title>Brightloop Service – Business Card</title>
<link href="https://fonts.googleapis.com/css2?family=Roboto+Slab:wght@400;600;700&display=swap" rel="stylesheet">
<style>
  :root {
    --stage: #222222;
    --ink: #000000;
    --paper: #ffffff;
    --accent: #ec1f27;
    --card-edge: #3a3a3a;
  }
  * { margin: 0; padding: 0; box-sizing: border-box; }
  html, body {
    width: 1189px; height: 1200px; overflow: hidden;
    background: var(--stage);
    font-family: "Roboto Slab", Georgia, serif;
  }
  .card {
    position: absolute; left: 171px; width: 856px; height: 488px;
    border: 1px solid var(--card-edge);
    box-shadow: 0 2px 6px rgba(0,0,0,.5);
    overflow: hidden;
  }
  .card--front { top: 68px; background: var(--ink); }
  .card--back { top: 626px; background: var(--paper); }

  .brand-mark {
    position: absolute; left: 0; right: 0; text-align: center;
    color: var(--accent); font-weight: 700;
  }
  .card--front .brand-mark { top: 290px; font-size: 72px; letter-spacing: 2px; }
  .brand-circle {
    position: absolute; left: 50%; top: 70px; width: 190px; height: 190px;
    margin-left: -95px; border: 3px solid var(--paper); border-radius: 50%;
  }
  .company-name {
    position: absolute; left: 0; right: 0; top: 400px; text-align: center;
    color: var(--paper); font-weight: 700; font-size: 32px;
    font-variant: small-caps; letter-spacing: 2px;
  }

  .back-panel {
    position: absolute; left: 0; top: 0; width: 420px; height: 100%;
    background: var(--ink);
  }
  .back-panel .brand-circle { top: 100px; }
  .back-panel .brand-mark { top: 320px; font-size: 64px; letter-spacing: 2px; }
  .accent-stripe {
    position: absolute; left: 420px; top: 0; width: 8px; height: 100%;
    background: var(--accent);
  }

  .contact { position: absolute; left: 488px; top: 98px; color: var(--ink); }
  .person-name { font-size: 30px; font-weight: 600; line-height: 1; }
  .person-title { font-size: 21px; color: var(--accent); line-height: 1.2; margin-top: 2px; }
  .address { font-size: 21px; line-height: 29px; margin-top: 26px; }
  .lines { list-style: none; margin-top: 22px; font-size: 21px; }
  .lines li { display: flex; align-items: center; height: 31px; }
  .lines svg { width: 22px; height: 20px; margin-right: 16px; fill: var(--accent); }
  .web { font-size: 21px; margin-top: 16px; }
  .web span { color: var(--accent); }
</style>
</head>
<body>

<section class="card card--front">
  <div class="brand-circle"></div>
  <div class="brand-mark">BLS</div>
  <div class="company-name">Brightloop Service</div>
</section>

<section class="card card--back">
  <div class="back-panel">
    <div class="brand-circle"></div>
    <div class="brand-mark">BLS</div>
  </div>
  <div class="accent-stripe"></div>

  <div class="contact">
    <h1 class="person-name">Colin Marsh</h1>
    <p class="person-title">service technician</p>
    <p class="address">1875 Carrow Lane NW<br>Edmonton AB T5K 2P4</p>
    <ul class="lines">
      <li>
        <svg viewBox="0 0 22 20" aria-hidden="true"><rect x="6" y="0" width="10" height="20" rx="2"/><rect x="8" y="3" width="6" height="5" fill="#fff"/></svg>
        555-014-2286
      </li>
      <li>
        <svg viewBox="0 0 22 20" aria-hidden="true"><path d="M1 7c0-3 4-5 10-5s10 2 10 5l-4 1-1-3H6L5 8z"/><path d="M4 18l3-9h8l3 9z"/></svg>
        555-018-7731
      </li>
      <li>
        <svg viewBox="0 0 22 20" aria-hidden="true"><rect x="0" y="3" width="22" height="15"/><path d="M1 4l10 8 10-8" stroke="#fff" stroke-width="2" fill="none"/></svg>
        hello@brightloopservice.ca
      </li>
    </ul>
    <p class="web">www.<span>brightloopservice</span>.ca</p>
  </div>
</section>

</body>
</html>
```